Dietitian needs awesome business card

I need a contemporary design that's eye catching but professional.
My card is to given to doctors, specialists and patients alike.
I manage patients with chronic diseases
I have uploaded my logo and current business card, I would also like the other Certified Clinical Nutritionist logo incorporated into the design

Target Market(s)

Doctors, specialists and patients

Industry/Entity Type

Healthcare

Contact Information for Business Card

www.brightfieldnutrition.com.au
Ph: 0427 561 903
Fax: 6457 2183
email: marcus.k.diet@fernmail.com
Space on the back of the card with: Appointment date, Appointment time and appointment location

Font styles to use
Serif

Colors
fbee3e
876aae
ffc214

Requirements
Must have
• My Logo
• Certified Clinical Nutritionist Logo
• My 4 locations - Pinebrook Medical Centre, North Corrin Health, Hollis Medical, Ashcombe Doctors Surgery
Nice to have
• I like the colours in my current business card

```html
<!DOCTYPE html>
<html lang="en">
<head>
<meta charset="utf-8">
<title>Brightfield Nutrition &amp; Dietetics – Business Card</title>
<link href="https://fonts.googleapis.com/css2?family=Jost:wght@400;500&display=swap" rel="stylesheet">
<style>
:root{
  --stage:#e9eaec;
  --card:#ffffff;
  --navy:#1f2d8c;
  --green:#a9c63d;
  --green-soft:#eef3e6;
  --orange:#f47d20;
  --rule:#9aa0b4;
  --blade-light:#dfe3ea;
  --blade-dark:#2f6fd0;
}
*{box-sizing:border-box;margin:0;padding:0}
html,body{width:1200px;height:886px;overflow:hidden}
body{background:var(--stage);font-family:"Jost",sans-serif;color:var(--navy);position:relative}
.card{position:absolute;left:300px;width:600px;height:367px;background:var(--card);border-radius:20px;overflow:hidden;box-shadow:0 4px 14px rgba(0,0,0,.12)}
.card--back{top:46px}
.card--front{top:473px}

/* brand lockup */
.brand{position:absolute;display:flex;align-items:center;gap:10px}
.brand__dot{width:44px;height:44px;border-radius:50%;background:var(--green);flex:none}
.brand__text{color:var(--navy);font-weight:400;line-height:1}
.brand__name{display:block;font-size:36px}
.brand__tag{display:block;font-size:13px;margin-top:3px;letter-spacing:.5px}

/* back side */
.back__wash{position:absolute;inset:0;background:linear-gradient(100deg,var(--green-soft) 0%,#f7f9f4 45%,#fff 75%)}
.card--back .brand{top:34px;right:40px}
.card--back .brand__dot{width:36px;height:36px}
.card--back .brand__name{font-size:30px}
.card--back .brand__tag{font-size:11px}
.back__rule{position:absolute;left:40px;right:40px;height:1px;background:var(--rule)}
.field{position:absolute;font-size:16px;font-weight:500;display:flex;align-items:flex-end;gap:8px}
.field__line{flex:1;height:1px;background:var(--rule);margin-bottom:4px}
.field__unit{font-size:13px}
.locations{position:absolute;list-style:none;font-size:14px;color:#333a5c}
.locations li{display:flex;align-items:center;gap:8px;margin-bottom:5px}
.tickbox{width:13px;height:13px;border:1.5px solid var(--navy);flex:none}

/* front side */
.front__panel{position:absolute;top:0;right:0;bottom:0;width:58%;background:var(--green)}
.front__knife{position:absolute;top:0;bottom:0;left:40%;width:42px;background:linear-gradient(90deg,var(--blade-light),var(--blade-dark))}
.card--front .brand{left:40px;top:196px}
.holder{position:absolute;right:36px;top:46px;text-align:right}
.holder__name{font-size:26px;font-weight:500;color:var(--navy)}
.holder__role{font-size:17px;color:#fff;margin-top:2px}
.badge{position:absolute;right:36px;top:120px;width:110px;height:48px;border-radius:4px;background:var(--orange)}
.badge::after{content:"";position:absolute;right:8px;top:7px;width:34px;height:34px;border-radius:50%;background:#fff}
.contact{position:absolute;right:30px;top:218px;list-style:none;text-align:right}
.contact li{display:flex;justify-content:flex-end;align-items:center;gap:10px;font-size:17px;color:#fff;height:26px}
.contact svg{width:16px;height:16px;flex:none}
</style>
</head>
<body>

<section class="card card--back" aria-label="Card back: appointment details">
  <div class="back__wash" role="img" aria-label="Faint photograph of fresh vegetables"></div>
  <div class="brand">
    <span class="brand__dot"></span>
    <span class="brand__text"><span class="brand__name">Brightfield</span><span class="brand__tag">Nutrition &amp; Dietetics</span></span>
  </div>
  <div class="back__rule" style="top:128px"></div>
  <div class="back__rule" style="top:166px"></div>
  <div class="field" style="left:40px;right:330px;top:208px"><span>Date :</span><span class="field__line"></span></div>
  <div class="field" style="left:300px;right:40px;top:208px"><span>Time :</span><span class="field__line"></span><span class="field__unit">AM/PM</span></div>
  <ul class="locations" style="left:40px;top:262px">
    <li><span class="tickbox"></span>Pinebrook Medical Centre</li>
    <li><span class="tickbox"></span>North Corrin Health</li>
  </ul>
  <ul class="locations" style="left:300px;top:262px">
    <li><span class="tickbox"></span>Ashcombe Doctors Surgery</li>
    <li><span class="tickbox"></span>Hollis Medical</li>
  </ul>
</section>

<section class="card card--front" aria-label="Card front: contact details">
  <div class="front__panel"></div>
  <div class="front__knife" role="img" aria-label="Illustration of a chef's knife blade"></div>
  <div class="brand">
    <span class="brand__dot"></span>
    <span class="brand__text"><span class="brand__name">Brightfield</span><span class="brand__tag">Nutrition &amp; Dietetics</span></span>
  </div>
  <div class="holder">
    <p class="holder__name">Marcus Kellaway</p>
    <p class="holder__role">Nutritionist &amp; Chef</p>
  </div>
  <div class="badge" role="img" aria-label="Certified Clinical Nutritionist badge"></div>
  <ul class="contact">
    <li>0427 561 903
      <svg viewBox="0 0 16 16" aria-hidden="true"><path fill="#1f2d8c" d="M3.5 1.5l2.5 0 1 3.2-1.6 1.2a8 8 0 0 0 4.7 4.7l1.2-1.6 3.2 1v2.5c0 .8-.7 1.5-1.5 1.5A12.5 12.5 0 0 1 2 3c0-.8.7-1.5 1.5-1.5z"/></svg></li>
    <li>6457 2183
      <svg viewBox="0 0 16 16" aria-hidden="true"><rect x="4" y="1" width="8" height="5" fill="#fff" stroke="#1f2d8c"/><rect x="1" y="6" width="14" height="7" rx="1" fill="#1f2d8c"/><rect x="4" y="11" width="8" height="4" fill="#fff" stroke="#1f2d8c"/></svg></li>
    <li>marcus.k.diet@fernmail.com
      <svg viewBox="0 0 16 16" aria-hidden="true"><rect x="1" y="3" width="14" height="10" fill="#1f2d8c"/><path d="M1 3l7 6 7-6" fill="none" stroke="#fff" stroke-width="1.3"/></svg></li>
    <li>www.brightfieldnutrition.com.au
      <svg viewBox="0 0 16 16" aria-hidden="true"><circle cx="8" cy="8" r="7" fill="#1f2d8c"/><path d="M1 8h14M8 1c3 3 3 11 0 14M8 1c-3 3-3 11 0 14" fill="none" stroke="#fff" stroke-width="1"/></svg></li>
  </ul>
</section>

</body>
</html>
```